Visualisation Software brochure

i need a sales brochure for a new visualisation software company called Lumora Studio Max.
The software has been specifically designed for manufacturers, distributers and retailers in the design / décor / furnishing / building industries. It allows customers can then import unlimited numbers of digital photos of rooms from their own home or take advantage of a library of pre-made photos, and then render different products from your catalogue into that photo to see what the finished look will be.
i have attached:
1) a mock up of the home page of the website
2) example of brochure wording that i have put together (although i am a little unsure about what other words i can add - so any suggestions here would be good)
3) i have attached some examples of other brochures that i like and would like similar designs
I am after a classy brochure used by a large corporate technology company that is given to executives and gives an impression of quality, trustworthiness and innovation.
• the colour blue as per the colours on my website mock up provided in the design brief
• I like simple, smart, clean and uncluttered design
• I like simple, clean and uncluttered design
• I like pictures that fit in with my technology (whether that be home and interior design, mixing virtual world and real world, visualising an idea) rather than basic stock of corporate people
Updates
Target Market(s)
marketing professionals
Industry/Entity Type
Software
Font styles to use
Look and feel
Each slider illustrates characteristics of the customer's brand and the style your logo design should communicate.

```html
<!DOCTYPE html>
<html lang="en">
<head>
<meta charset="utf-8">
<title>Lumora Studio Max – Brochure</title>
<link rel="stylesheet" href="https://fonts.googleapis.com/css2?family=Titillium+Web:wght@300;400;600&display=swap">
<style>
:root{
  --blue:#2a8de4;
  --ink:#4a4a4a;
  --paper:#ffffff;
  --backdrop:#ffffff;
  --rule:#2a8de4;
  --edge:#e4e6ea;
  --dark:#1b1b1b;
}
*{margin:0;padding:0;box-sizing:border-box}
html,body{width:953px;height:1200px;overflow:hidden;background:var(--backdrop)}
body{position:relative;font-family:"Titillium Web",Arial,sans-serif;color:var(--ink)}
.page{position:absolute;background:var(--paper);border:1px solid var(--edge);overflow:hidden}
.page-cover{left:490px;top:28px;width:393px;height:555px}
.page-left{left:92px;top:598px;width:394px;height:557px}
.page-right{left:487px;top:598px;width:396px;height:557px}
.abs{position:absolute}
.heading{font-weight:300;color:var(--blue);line-height:1.0}
.body-copy{font-size:5.6px;line-height:8px;font-weight:300;color:var(--ink);text-align:justify}
.body-copy p{margin-bottom:7px}
.benefits p{margin-bottom:10px}
.cover-copy{font-size:7.4px;line-height:16.5px}
.page-number{font-size:9px;color:var(--blue);font-weight:300}
.brand-mark{display:flex;align-items:center;gap:4px;font-weight:600;font-size:11px;color:var(--blue)}
.brand-mark .dot{width:22px;height:22px;border-radius:50%;background:var(--blue)}
.photo{position:absolute}
.lead-blue{font-size:11.3px;line-height:15.8px;color:var(--blue);font-weight:300;text-align:justify}
.lead-blue strong{font-weight:600}
.intro-blue{font-size:7.3px;line-height:8.2px;color:var(--blue);font-weight:300;text-align:justify}
.caps-heading{font-size:12.5px;font-weight:400;color:var(--blue);letter-spacing:.2px}
svg.rules{position:absolute;left:0;top:0;overflow:visible}
</style>
</head>
<body>

<section class="page page-cover">
  <div class="abs brand-mark" style="right:18px;top:22px"><span>LSM</span><span class="dot"></span></div>
  <h1 class="abs heading" style="left:34px;top:76px;font-size:17.5px">Innovation<br>redefining retail</h1>
  <svg class="rules" width="393" height="555">
    <polyline points="160,104 255,104 255,397" fill="none" stroke="var(--rule)" stroke-width="1"/>
    <circle cx="255" cy="397" r="2.5" fill="var(--rule)"/>
  </svg>
  <div class="abs body-copy cover-copy" style="left:34px;top:122px;width:207px">
    <p>We have a product that is rapidly being seen as the next market leader in interactive visualisation software. Lumora Studio Max has been developed as an all-inclusive, easy-to-use solution that has been specifically designed for retail businesses within the design, décor, flooring, furnishing, building / renovation and real estate industries.</p>
  </div>
  <p class="abs lead-blue" style="left:34px;top:250px;width:207px"><strong>Lumora Studio Max</strong> is an innovative and powerful web and/or app-based platform that delivers you the capability to positively transform the overall retail experience of your customers as well as your bottom-line as it helps your customers achieve results by being able to visualise and conceptualise in real time how wonderful their real rooms or new homes could look with your products.</p>
  <div class="photo" role="img" aria-label="Software shown on desktop, laptop, tablet and phone screens" style="left:105px;top:398px;width:242px;height:130px;background:linear-gradient(180deg,#e9ecef,#bfc4ca);border-radius:4px"></div>
  <span class="abs page-number" style="left:32px;top:532px">1</span>
</section>

<section class="page page-left">
  <div class="photo" role="img" aria-label="Modern dining room interior with pendant lights and white chairs" style="left:0;top:0;width:394px;height:225px;background:linear-gradient(160deg,#c9d3dc 0%,#9aa7b3 55%,#5b5048 100%)"></div>
  <div class="abs" style="left:213px;top:142px;width:181px;height:83px;background:var(--paper)"></div>
  <h2 class="abs heading" style="left:223px;top:151px;font-size:17px">The virtualised<br>solution</h2>
  <svg class="rules" width="394" height="557">
    <circle cx="303" cy="102" r="10" fill="none" stroke="#fff" stroke-width="2"/>
    <circle cx="303" cy="102" r="5" fill="#fff" stroke="var(--rule)" stroke-width="1"/>
    <polyline points="313,102 354,102 354,184 288,184" fill="none" stroke="var(--rule)" stroke-width="1"/>
  </svg>
  <p class="abs intro-blue" style="left:223px;top:192px;width:165px">Having your own branded virtual design software embedded on your website or accessible via an Orbitron and/or Pomelo app will help bridge the gap between your customers' design dreams and your products. Our software helps solve one of the biggest problems many experience whilst redecorating or designing their home, which is despite looking at numerous samples, most cannot visualise or conceptualise what the finished look will be.</p>
  <div class="abs body-copy" style="left:223px;top:282px;width:165px">
    <p>It doesn't matter what business you're in. Your customers will be able to visualise all possible product combinations for their new home – it just depends on your range. The software can easily handle 'flat surface products' including roofing, cladding, garage doors, windows and driveways/pathways to interior products such as carpet, tiles, timber and laminate flooring, doors, art works, bench tops and splash-backs. Importantly, our technology can also handle any product in 3D – whether it be furniture, lighting, floor rugs, curtains / blinds, wardrobes, household items, kitchen cabinets and bathroom fixtures. A truly unique feature allows customers to simply delete the existing item from their photo and replace it with another product from your catalogue without removing any item physically.</p>
    <p>Today's consumer doesn't just rely on technological gimmicks such as augmented reality or one in-store visit before making important investment decisions. With so much competition in the marketplace consumers are more driven than ever to shop around with the amount and quality of value-adding service the real deal breaker rather than price.</p>
    <p>It has become more about initiating the education of your customer versus waiting for them to ask for assistance. Using our technology can increase sales conversion rates as once customers have identified what products they would like to purchase they come to you as educated buyers, already having experienced a fantastic customer interaction with your brand.</p>
  </div>
  <h2 class="abs heading" style="left:61px;top:242px;font-size:16.5px;line-height:1.07">The challenge<br>for both customers<br>and retailers</h2>
  <div class="abs body-copy" style="left:61px;top:303px;width:148px">
    <p>Gone are the days when all you needed was a showroom, a product line and a business card. Customers are better informed, more interactive, and more selective than ever before. With access to a range of new technologies and a wide variety of online resources, these connected consumers are increasingly demanding a dynamic, seamless, integrated, consistent, accessible and personalised experience with your brand across all online, bricks-and-mortar and mobile channels.</p>
    <p>The customer must be empowered to interact across all touchpoints and channels; they want to browse and buy on their own schedules and retailers must offer equally accurate and immediate access to products and customer service. Consumers want to be involved and be given the tools, advice and confidence to create unique, personal spaces – meaning companies need to feed this design dream and appealing to their vision is essential. The shopping experience should be built around the new reality that most consumers make their browsing and purchasing commitments online, often before they ever see the product in person.</p>
    <p>Amid ongoing economic uncertainty, true omni-channel retailers need to continue to focus on understanding the customer psyche and leveraging innovation to drive loyalty and customer engagement and ultimately increase sales.</p>
  </div>
  <span class="abs page-number" style="left:30px;top:534px">2</span>
</section>

<section class="page page-right">
  <div class="photo" role="img" aria-label="Person touching a glowing network of connected nodes over a night city" style="left:0;top:0;width:396px;height:202px;background:linear-gradient(170deg,#3a4552 0%,#1d2633 60%,#0f141c 100%)"></div>
  <svg class="rules" width="396" height="557">
    <polygon points="60,202 78,202 69,218" fill="var(--dark)"/>
    <polyline points="188,235 213,235 213,367 228,367" fill="none" stroke="var(--rule)" stroke-width="1"/>
  </svg>
  <h3 class="abs caps-heading" style="left:67px;top:224px">RETAILER BENEFITS</h3>
  <div class="abs body-copy benefits" style="left:67px;top:248px;width:145px;text-align:left">
    <p>Be the market innovator and leader by combining technology and a dynamic, seamless, integrated and consistent level of customer service across all online, bricks-and-mortar and mobile channels that delivers the big wow factor.</p>
    <p>Extend your reach – don't limit your technology footprint by only using Pomelo apps – our solution leverages and optimises all mobile devices and desktops (PomeloOS, Orbitron, Web). This equates to a larger watershed of customers and more sales.</p>
    <p>Increase brand engagement as our bespoke and scalable visualisation application will help customers build a relationship with your company, brand, and products and then share that experience within their social circles.</p>
    <p>Understand buyer behaviour by receiving real usage statistics to obtain valuable insight about your customers and conduct trend analysis to determine how your future strategies can further enhance your bottom line.<br>Increased sales to further grow your business.</p>
    <p>Maximise the exposure of your products by uploading your entire product catalogue into a visualisation software that makes them look real.</p>
  </div>
  <h3 class="abs caps-heading" style="left:230px;top:356px">CONSUMER BENEFITS</h3>
  <div class="abs body-copy benefits" style="left:230px;top:378px;width:160px;text-align:left">
    <p>Reduce your customer's purchase anxiety as they will have the knowledge that the products they are choosing from your range are the right choice.</p>
    <p>Greater flexibility in the way they shop by being open 24/7 and being able to engage with your brand when they want and how they want. Happier customers and hence more sales.</p>
    <p>An easy-to-use interface along with guided help and tutorials for those less confident with technology.</p>
    <p>Being able to make informed purchasing decisions as they can easily compare a large range of your products at the touch of a computer key.</p>
    <p>Improved personalised buying experience by enabling customers to use photos of their own personal spaces and incorporate your products.</p>
  </div>
  <span class="abs page-number" style="left:30px;top:534px">3</span>
</section>

</body>
</html>
```